Novexa company website, a website for employment for people with autism

The website will make a match between people and jobs, mainly in the graphical sector, but also other sectors.
The name of the company is novexa and automates jobs with people that are on the autism spectrum.
The whole matchmaking and feedback process and so doesn't have to be in this prototype, we just want the general information pages and to convey a great look and brand identity that we will keep in the other pages to be developed. The website must be made with Wordpress, since the backend will be developed in Wordpress too.
It is a social project that wants to create possibilites for people with ASS to work from home for an employer or to do a variety of tasks for different customers.
The people we hire are generally not on the regular job market or have difficulty finding a job and "selling themselves"

Target Market(s)

matchmaking between talent (with ASS) and employers / jobs

Number of Pages Required

5+ page

Font styles to use
Sans Serif

Colors
ec1f27
e34298
a64599
6b449b
0355a3
0792cd

Requirements
Must have
• A stunning landing pages
• Integrate our logo and must match with what will do. We want a clean, modern, minimalistic, sleek website that radiates creativity and good looks.
• We have one page describing what we can do for customers, one page for people with ASS that would like to be candidates (our approach, learning program, ...), two pages that are addressed to partners who want to cooperate: the one's that can assist with autism related assistance and the one's that can help with the job coaching.
Nice to have
• In our logo are many colors as we embrace diversity and want to show that. Out main branding colors are red (for action) and blue for stability and will all gradients that go with it. Mainly white or black (or anthracite) for other parts
Should not have
• We want a modern and minimalistic design, no fluffy designs with lots of ornaments.

```html
<!DOCTYPE html>
<html lang="en">
<head>
<meta charset="utf-8">
<title>Novexa</title>
<link rel="stylesheet" href="https://fonts.googleapis.com/css2?family=Montserrat:wght@500;600;700;800&family=Lato:wght@400;700&display=swap">
<style>
:root{
  --red:#ec1f27;
  --pink:#e34298;
  --magenta:#c0267f;
  --violet:#a64599;
  --purple:#6b449b;
  --blue:#0355a3;
  --sky:#0792cd;
  --lime:#c7c642;
  --teal:#4fb9b4;
  --ink:#222222;
  --anthracite:#1d1c1d;
  --grey-bg:#f4f4f4;
  --text-grey:#666666;
  --white:#ffffff;
}
*{margin:0;padding:0;box-sizing:border-box}
html,body{width:1200px;height:3209px;overflow:hidden}
body{font-family:"Lato",sans-serif;color:var(--ink);background:var(--white);position:relative}
.heading{font-family:"Montserrat",sans-serif}
section,header,footer{position:absolute;left:0;width:1200px}

/* Hero */
.hero{top:0;height:730px;overflow:hidden}
.hero-backdrop{position:absolute;inset:0;background:radial-gradient(ellipse at 62% 55%,#5b5d63 0%,#34353a 40%,#141416 80%)}
.hero-shape{position:absolute;left:0;top:0}
.site-nav{position:absolute;top:0;left:0;width:1200px;height:100px}
.brand{position:absolute;left:156px;top:30px;font-family:"Montserrat",sans-serif;font-weight:600;font-size:34px;letter-spacing:3px;color:var(--white)}
.nav-links{position:absolute;right:158px;top:40px;display:flex;gap:37px;list-style:none}
.nav-links li{font-family:"Montserrat",sans-serif;font-weight:700;font-size:15px;color:var(--white)}
.hero-title{position:absolute;top:312px;left:0;width:1200px;text-align:center;color:var(--white);font-family:"Montserrat",sans-serif;font-weight:700}
.hero-title .line-1{display:block;font-size:48px;line-height:60px}
.hero-title .line-2{display:block;font-size:32px;line-height:42px}

/* About */
.about{top:730px;height:618px;background:var(--white)}
.section-title{position:absolute;display:flex;align-items:center;font-family:"Montserrat",sans-serif;font-weight:700}
.about .section-title{left:148px;top:100px;font-size:37px;color:var(--magenta)}
.section-title svg{position:absolute;left:0;top:50%;transform:translateY(-50%)}
.section-title span{position:relative}
.about .section-title .accent{color:var(--red)}
.copy{position:absolute;font-size:18.5px;line-height:27px}
.copy p+p{margin-top:27px}
.about .copy{left:156px;top:184px;width:480px;color:var(--ink)}
.btn{position:absolute;display:flex;align-items:center;justify-content:center;border-radius:29px;font-family:"Montserrat",sans-serif;font-weight:700;font-size:16px;letter-spacing:.5px}
.about .btn{left:154px;top:376px;width:188px;height:58px;border:2px solid var(--red);color:var(--red)}
.about-art{position:absolute;left:0;top:0}

/* Services */
.services{top:1348px;height:562px;background:var(--anthracite)}
.services-art{position:absolute;left:0;top:0}
.services .section-title{left:616px;top:120px;font-size:32px;color:var(--white)}
.services .copy{left:616px;top:198px;width:480px;color:var(--white)}
.services .btn{left:612px;top:382px;width:186px;height:56px;background:var(--white);color:var(--red)}

/* Blog */
.blog{top:1910px;height:603px;background:var(--grey-bg)}
.blog .section-title{left:0;width:1200px;justify-content:center;top:50px;font-size:35px;color:var(--blue)}
.blog .section-title .wrap{position:relative;padding-left:0}
.blog .section-title .accent{color:var(--blue);font-weight:800}
.blog .section-title .lead{color:var(--sky)}
.cards{position:absolute;top:158px;left:158px;display:flex;gap:30px}
.card{width:283px;height:349px;background:var(--white);box-shadow:0 2px 8px rgba(0,0,0,.12);position:relative}
.card-media{height:167px;width:100%}
.media-1{background:linear-gradient(135deg,#5b6672,#c9ced6 55%,#8a8f96)}
.media-2{background:linear-gradient(135deg,#9fb2c4,#d7e0ea 50%,#6e8195)}
.media-3{background:linear-gradient(135deg,#3d4a2e,#8a7a3a 45%,#2a3347)}
.card-date{position:absolute;left:24px;top:150px;background:var(--white);padding:2px 14px 0;font-family:"Montserrat",sans-serif;font-weight:700;font-size:13px;color:var(--red);height:22px;line-height:22px}
.card-title{margin:24px 24px 0;font-family:"Montserrat",sans-serif;font-weight:700;font-size:14.5px;line-height:20px;color:#1b7ac0}
.card-text{margin:14px 24px 0;font-size:12px;line-height:15px;color:var(--text-grey)}
.card-more{margin:16px 24px 0;font-family:"Montserrat",sans-serif;font-weight:700;font-size:12.5px;color:var(--blue)}

/* Contact */
.contact{top:2513px;height:546px;background:linear-gradient(110deg,#5b2f8e 0%,#4a3c9a 35%,#2a64b6 70%,#1383cf 100%);color:var(--white)}
.contact .section-title{left:160px;top:80px;font-size:30px;color:var(--white)}
.contact-list{position:absolute;left:160px;top:170px;list-style:none}
.contact-item{position:relative;padding-left:65px;margin-bottom:26px}
.contact-item svg{position:absolute;left:4px;top:8px}
.contact-label{font-family:"Montserrat",sans-serif;font-weight:700;font-size:16px;line-height:22px}
.contact-value{font-size:16.5px;line-height:27px}
.contact-form{position:absolute;left:522px;top:105px;width:535px}
.field{display:block;width:535px;height:49px;background:var(--white);margin-bottom:9px;padding:14px 22px;font-size:14.5px;color:#555}
.field.message{height:114px}
.submit{position:absolute;left:2px;top:306px;width:173px;height:56px;background:#e0287d;color:var(--white);font-family:"Montserrat",sans-serif;font-weight:700;font-size:19px;display:flex;align-items:center;justify-content:center}

/* Footer */
.site-footer{top:3059px;height:150px;background:var(--white)}
.footer-brand{position:absolute;left:160px;top:52px;font-family:"Montserrat",sans-serif;font-weight:700;font-size:22px;color:var(--purple)}
.footer-links{position:absolute;left:344px;top:48px;display:flex;gap:36px;list-style:none}
.footer-links li{font-family:"Montserrat",sans-serif;font-weight:700;font-size:15px;color:#555}
.copyright{position:absolute;left:344px;top:86px;font-size:13px;color:#777}
.social{position:absolute;left:878px;top:41px;display:flex;gap:8px;list-style:none}
.social li{width:32px;height:32px;border-radius:50%}
.social .s1{background:#3b5998}.social .s2{background:#1da1f2}.social .s3{background:#4d5fa8}.social .s4{background:#0e76a8}
</style>
</head>
<body>

<header class="hero">
  <div class="hero-backdrop" role="img" aria-label="Photo of hands typing on a laptop keyboard in low light"></div>
  <svg class="hero-shape" width="1200" height="730" viewBox="0 0 1200 730">
    <defs>
      <linearGradient id="heroHex" x1="0" y1="0" x2="0" y2="1">
        <stop offset="0" stop-color="#a64599"/>
        <stop offset="1" stop-color="#ec1f27"/>
      </linearGradient>
    </defs>
    <polygon points="590,128 789,243 789,473 590,588 391,473 391,243" fill="none" stroke="url(#heroHex)" stroke-width="11"/>
    <circle cx="590" cy="272" r="33" fill="#ffffff"/>
    <circle cx="590" cy="272" r="27" fill="#1b1b1d"/>
    <polygon points="583,259 583,285 603,272" fill="#ffffff"/>
    <line x1="590" y1="462" x2="590" y2="668" stroke="#ffffff" stroke-width="2"/>
    <polyline points="582,672 590,680 598,672" fill="none" stroke="#ffffff" stroke-width="2"/>
    <polyline points="582,682 590,690 598,682" fill="none" stroke="#ffffff" stroke-width="2"/>
    <polyline points="582,692 590,700 598,692" fill="none" stroke="#ffffff" stroke-width="2"/>
  </svg>
  <nav class="site-nav">
    <div class="brand">NOVEXA</div>
    <ul class="nav-links">
      <li>ABOUT US</li><li>SERVICES</li><li>JOBS</li><li>BLOG</li><li>CONTACT</li>
    </ul>
  </nav>
  <h1 class="hero-title">
    <span class="line-1">AUTOMATES JOBS WITH</span>
    <span class="line-2">PEOPLE THAT ARE ON THE</span>
    <span class="line-2">AUTISM SPECTRUM</span>
  </h1>
</header>

<section class="about">
  <svg class="about-art" width="1200" height="618" viewBox="0 0 1200 618">
    <defs>
      <linearGradient id="aboutBorder" x1="0" y1="0" x2="1" y2="1">
        <stop offset="0" stop-color="#6b449b"/>
        <stop offset="1" stop-color="#0792cd"/>
      </linearGradient>
      <linearGradient id="aboutRed" x1="0" y1="0" x2="0" y2="1">
        <stop offset="0" stop-color="#ec1f27"/>
        <stop offset="1" stop-color="#6b449b"/>
      </linearGradient>
      <linearGradient id="aboutGreen" x1="1" y1="0" x2="0" y2="1">
        <stop offset="0" stop-color="#4fb9b4"/>
        <stop offset="1" stop-color="#c7c642"/>
      </linearGradient>
      <linearGradient id="aboutPhoto" x1="0" y1="0" x2="1" y2="1">
        <stop offset="0" stop-color="#c8b9a4"/>
        <stop offset=".5" stop-color="#6f5b55"/>
        <stop offset="1" stop-color="#2e3442"/>
      </linearGradient>
    </defs>
    <polygon points="783,178 936,266 936,443 783,532 630,443 630,266" fill="none" stroke="url(#aboutRed)" stroke-width="12"/>
    <polygon points="1003,210 1170,307 1170,500 1003,596 836,500 836,307" fill="none" stroke="url(#aboutGreen)" stroke-width="10"/>
    <polygon points="915,25 1104,134 1104,344 915,453 726,344 726,134" fill="url(#aboutPhoto)" stroke="url(#aboutBorder)" stroke-width="14" role="img" aria-label="Photo of a young man working on a laptop in an office"/>
  </svg>
  <h2 class="section-title">
    <svg width="58" height="66" viewBox="0 0 58 66"><polygon points="29,3 55,18 55,48 29,63 3,48 3,18" fill="none" stroke="#c0267f" stroke-width="3"/></svg>
    <span style="left:18px">ABOUT <span class="accent">NOVEXA</span></span>
  </h2>
  <div class="copy">
    <p>Pellentesque faucibus Ut accumsan ultricies elit Maecenas at justo id velit placerat molestie Donec dictum lectus non odio Cras a ante vitae enim iaculis aliquam</p>
    <p>Mauris nunc quam venenatis nec euismod sit amet egestas placerat est Pellentesque habitant morbi tristique</p>
  </div>
  <div class="btn">LEARN MORE</div>
</section>

<section class="services">
  <svg class="services-art" width="1200" height="562" viewBox="0 0 1200 562">
    <defs>
      <linearGradient id="servBorder" x1="0" y1="0" x2="0" y2="1">
        <stop offset="0" stop-color="#a64599"/>
        <stop offset="1" stop-color="#ec1f27"/>
      </linearGradient>
      <linearGradient id="servPhoto" x1="0" y1="0" x2="1" y2="1">
        <stop offset="0" stop-color="#a89a8c"/>
        <stop offset=".5" stop-color="#3f7fbf"/>
        <stop offset="1" stop-color="#2b2b30"/>
      </linearGradient>
    </defs>
    <polygon points="339,57 532,168 532,392 339,503 146,392 146,168" fill="url(#servPhoto)" stroke="url(#servBorder)" stroke-width="13" role="img" aria-label="Photo of a man with a headset working at a computer"/>
  </svg>
  <h2 class="section-title">
    <svg width="56" height="64" viewBox="0 0 56 64"><polygon points="28,3 53,17 53,47 28,61 3,47 3,17" fill="none" stroke="#ffffff" stroke-width="3"/></svg>
    <span style="left:22px">OUR SERVICES</span>
  </h2>
  <div class="copy">
    <p>Pellentesque faucibus Ut accumsan ultricies elit Maecenas at justo id velit placerat molestie Donec dictum lectus non odio Cras a ante vitae enim iaculis aliquam</p>
    <p>Mauris nunc quam venenatis nec euismod sit amet egestas placerat est Pellentesque habitant morbi tristique</p>
  </div>
  <div class="btn">LEARN MORE</div>
</section>

<section class="blog">
  <h2 class="section-title">
    <span class="wrap">
      <svg width="60" height="68" viewBox="0 0 60 68" style="left:-26px"><polygon points="30,3 57,18 57,50 30,65 3,50 3,18" fill="none" stroke="#0792cd" stroke-width="3"/></svg>
      <span><span class="lead">RECENT</span> <span class="accent">BLOGS</span></span>
    </span>
  </h2>
  <div class="cards">
    <article class="card">
      <div class="card-media media-1" role="img" aria-label="Photo of hands typing on a laptop"></div>
      <div class="card-date">JAN 29, 2019</div>
      <h3 class="card-title">Lorem ipsum dolor sit amet consectetuer adipiscing elit Nam</h3>
      <p class="card-text">Duis quam Nam eget lacus Aliquam erat volutpat Quisque dignissim congue leo Mauris vel lacus vitae felis</p>
      <p class="card-more">READ MORE &#8250;</p>
    </article>
    <article class="card">
      <div class="card-media media-2" role="img" aria-label="Photo of a laptop keyboard in bright light"></div>
      <div class="card-date">JAN 25, 2019</div>
      <h3 class="card-title">Lorem ipsum dolor sit amet consectetuer adipiscing elit Nam</h3>
      <p class="card-text">Duis quam Nam eget lacus Aliquam erat volutpat Quisque dignissim congue leo Mauris vel lacus vitae felis</p>
      <p class="card-more">READ MORE &#8250;</p>
    </article>
    <article class="card">
      <div class="card-media media-3" role="img" aria-label="Photo of a man in a suit standing in an office"></div>
      <div class="card-date">JAN 20, 2019</div>
      <h3 class="card-title">Lorem ipsum dolor sit amet consectetuer adipiscing elit Nam</h3>
      <p class="card-text">Duis quam Nam eget lacus Aliquam erat volutpat Quisque dignissim congue leo Mauris vel lacus vitae felis</p>
      <p class="card-more">READ MORE &#8250;</p>
    </article>
  </div>
</section>

<section class="contact">
  <h2 class="section-title">
    <svg width="54" height="62" viewBox="0 0 54 62"><polygon points="27,3 51,17 51,45 27,59 3,45 3,17" fill="none" stroke="#ffffff" stroke-width="3"/></svg>
    <span style="left:20px">CONTACT US</span>
  </h2>
  <ul class="contact-list">
    <li class="contact-item">
      <svg width="34" height="38" viewBox="0 0 34 38"><path d="M17 34 C17 34 5 21 5 13 A12 12 0 0 1 29 13 C29 21 17 34 17 34Z" fill="none" stroke="#fff" stroke-width="2"/><circle cx="17" cy="13" r="4.5" fill="none" stroke="#fff" stroke-width="2"/><ellipse cx="17" cy="35" rx="10" ry="2.5" fill="none" stroke="#fff" stroke-width="1.5"/></svg>
      <div class="contact-label">ADDRESS</div>
      <div class="contact-value">482 Harbor Lane Suite 7<br>Austin 78701 TX</div>
    </li>
    <li class="contact-item">
      <svg width="36" height="36" viewBox="0 0 36 36"><path d="M8 3 L14 9 L10 14 C12 19 17 24 22 26 L27 22 L33 28 L28 33 C16 32 4 20 3 8 Z" fill="none" stroke="#fff" stroke-width="2" stroke-linejoin="round"/></svg>
      <div class="contact-label">PHONE NUMBER</div>
      <div class="contact-value">555.014.2280</div>
    </li>
    <li class="contact-item">
      <svg width="38" height="30" viewBox="0 0 38 30"><rect x="2" y="3" width="34" height="24" fill="none" stroke="#fff" stroke-width="2"/><polyline points="2,3 19,17 36,3" fill="none" stroke="#fff" stroke-width="2"/><line x1="2" y1="27" x2="14" y2="14" stroke="#fff" stroke-width="1.5"/><line x1="36" y1="27" x2="24" y2="14" stroke="#fff" stroke-width="1.5"/></svg>
      <div class="contact-label">EMAIL ADDRESS</div>
      <div class="contact-value">info@novexajobs.com</div>
    </li>
  </ul>
  <div class="contact-form">
    <div class="field">Name</div>
    <div class="field">Email address</div>
    <div class="field">Phone</div>
    <div class="field message">Message</div>
    <div class="submit">SUBMIT</div>
  </div>
</section>

<footer class="site-footer">
  <div class="footer-brand">Novexa</div>
  <ul class="footer-links">
    <li>ABOUT US</li><li>SERVICES</li><li>JOBS</li><li>BLOG</li><li>CONTACT</li>
  </ul>
  <p class="copyright">© 2019 Company Name&nbsp; All right reserved</p>
  <ul class="social" aria-label="Social links">
    <li class="s1"></li><li class="s2"></li><li class="s3"></li><li class="s4"></li>
  </ul>
</footer>

</body>
</html>
```